Web Design Project for a Software & Consulting Company

We have just completed a recent ArtHerdly project for a new logo (see attached).
As the next stage of our rebranding we now require a website re-design to complement the new logo.
Our current site, http://www.corvinsoft.example was built in-house and does not come across as professional as we would like. We supply software and associated services to some of the world’s largest oil companies and we need our site to reflect that level of client.
We will also be posting another design project for brochures, PowerPoint slides and other materials very soon.
We would like designs for…
Home page
Product page
• TZQ
• BLV
• PNJ
Services
News page
About Us page
Contact Us page
Page for mobile devices that gives basic company and product information
Currently the site is small but we intend to increase content to include white papers etc. this should be taken into account when designing the navigation therefore we would prefer navigation through styled text links rather than images.
Colour schemes should broadly be taken from our new logo, where the dark blue and dark green from the left and right sides of the logo are the main colours, but other, brighter accent colours can be used to highlight sections or content.
Dark Blue = C:88, M:55, Y:44, K:28
Dark Green = C:87, M:53, Y:50, K:50
NB: Don’t use the logo on our current site, make sure you use the one attached.
We would prefer the final file format to be a layered PSD.
The site should be clean and professional and communicate the following...
• That we have a great depth and breadth of knowledge about our customers’ business, enabling us to deliver the best systems and solutions.
• That we are a leading provider of cost estimation and control solutions to the oil and gas industry.
• The benefits of our software and consulting services.
• Show that we deliver outstanding customer service and value with a very high level of professionalism
• The site should have no Flash and be able to self-adjust to fit any screen size.
Things to avoid …
• Obvious and clichéd oil industry imagery, no oil rigs
• Cartoon style graphics
Our Background
We are an integrated software and consulting organization specialising in the drilling side of the oil and gas industry. Simply put our software helps companies better understand, predict and communicate the cost of drilling wells.
We have 3 software products and a consulting offering consisting of…
• TZQ - Probabilistic time and cost software
• BLV – Cost tracking and reporting software
• PNJ – (currently known as DrillSavant) – Lessons learned software
• Consulting services
Our systems are in use in over 30 countries with a broad range of clients including: GN, Marovel, Dunt, Koruna, VELO Sirkami, FALUMI and Quintex.
Our current site can be found at www.corvinsoft.example
Our main competitors are
• http://www.drovanic.example/
• http://www.sumbrask.example/
• http://www.kve.example/services/software-solutions/p1-
Our depth of drilling knowledge, quality of software and collaboration with clients differentiate us form the competition.
We strive for very high levels of customer service.
We look forward to receiving your designs!
Updates
Thanks to all the designers who have submitted a design, we appreciate the effort.
We will do our best to give individual feedback on each design but given that many are quite similar we thought we would give some general feedback first.
Nearly all the designs submitted so far have been slight variations on…
-
Top Menu
-
Scrolling Photo Banner
-
4 Columns
-
Body
-
Deep Footer
These designs are well executed but they are basically the same layout as our existing site and while there is nothing inherently wrong with this layout we would like to see some designs that are a bit more innovative and different. We don’t really want just a polished version of our current site.
Thanks again,
CVS
Thanks to everyone who has submitted a design, the response has been great.
We are close to making a decision so if you are intending to submit a design please do it soon, the deadline is only a few days away.
Thanks again.
CVS
Target Market(s)
Mid to high level executives
Industry/Entity Type
Oil And Gas
Look and feel

```html
<!DOCTYPE html>
<html lang="en">
<head>
<meta charset="utf-8">
<title>CorvinSoft Technologies</title>
<link rel="stylesheet" href="https://fonts.googleapis.com/css2?family=PT+Sans:wght@400;700&display=swap">
<style>
:root{
  --teal:#2b7685;
  --teal-dark:#17495a;
  --ink:#1b1b1b;
  --cyan:#55c4df;
  --page:#ffffff;
  --bg-top:#cdcdcd;
  --bg-low:#ececec;
  --frame:#e2e2e2;
  --foot-a:#6f7f8a;
  --foot-b:#2d3944;
}
*{box-sizing:border-box;margin:0;padding:0}
html,body{width:900px;height:1200px;overflow:hidden}
body{position:relative;font-family:"PT Sans",Arial,sans-serif;color:var(--ink);
  background:linear-gradient(var(--bg-top) 0 372px,var(--bg-low) 372px)}
.abs{position:absolute}
.page{left:76px;top:0;width:750px;height:998px;background:var(--page);box-shadow:0 0 4px rgba(0,0,0,.2)}
.brand{left:92px;top:44px;display:flex;align-items:center;gap:8px;font-size:24px;font-weight:700;color:var(--teal-dark);letter-spacing:.5px}
.brand i{width:22px;height:22px;border-radius:50%;background:var(--teal)}
.search{left:624px;top:59px;width:178px;height:20px;border:1px solid #a8a8a8;border-radius:3px;font-size:9px;color:#999;padding:4px 10px;display:flex;justify-content:space-between}
.nav{left:92px;top:110px;width:718px;height:40px;background:linear-gradient(#3a8a98,var(--teal-dark));border-radius:2px}
.nav a{position:absolute;top:0;height:40px;line-height:40px;color:#fff;font-size:14px;text-decoration:none;transform:translateX(-50%)}
.nav .active{background:#123a47;width:105px;text-align:center}
.dropdown{left:226px;top:150px;width:105px;background:#0d0d0d;z-index:5}
.dropdown a{display:block;height:23px;line-height:23px;text-align:center;color:#fff;font-size:12px;text-decoration:none;border-bottom:1px solid #333}
.dropdown a:last-child{border-bottom:0}
.hero-frame{left:91px;top:173px;width:710px;height:295px;background:var(--frame)}
.hero-img{left:102px;top:185px;width:688px;height:268px;background:linear-gradient(90deg,#6f9ad6 0%,#a9c0df 40%,#c9d6e6 60%,#6f95c4 80%,#d3b43a 88%,#5b86c0 100%)}
.hero-card{left:102px;top:232px;width:461px;height:188px;background:rgba(235,242,250,.72)}
.hero-card h1{position:absolute;left:19px;top:9px;font-size:18px;line-height:25px;font-weight:400;text-transform:uppercase;color:#111;white-space:nowrap}
.hero-card p{position:absolute;left:21px;top:88px;font-size:12px;line-height:22px;width:400px}
.btn-read{left:120px;top:372px;width:138px;height:29px;border-radius:3px;background:linear-gradient(#fff,#d6d6d6);border:1px solid #bbb;font-size:12px;line-height:27px;text-align:center}
.ribbon{left:680px;top:390px}
h2.welcome{left:94px;top:488px;font-size:13px;font-weight:700}
.welcome-img{left:103px;top:518px;width:219px;height:110px;border-radius:8px;border:2px solid #d6d6d6;background:linear-gradient(#7aa3cf,#b9cde0 70%,#b7a888)}
.intro{left:333px;top:522px;width:465px;font-size:10px;line-height:16px}
.intro p+p{margin-top:15px}
.col{top:656px;width:164px}
.col h3{height:26px;line-height:26px;text-align:center;color:#fff;font-weight:400;font-size:14px;background:linear-gradient(#3a8a98,var(--teal-dark))}
.col .thumb{margin:13px 0 0 6px;width:150px;height:72px}
.col p{margin:6px 0 0 6px;font-size:9.6px;line-height:16px;white-space:nowrap}
.col .more{margin:14px 0 0 6px;width:90px;height:24px;border-radius:12px;background:linear-gradient(#fff,#d2d2d2);border:1px solid #bbb;font-size:12px;line-height:22px;text-align:center}
h2.clients{left:94px;top:870px;font-size:12px;font-weight:700}
.client-box{left:93px;top:895px;width:717px;height:94px;background:#e4e4e4;border-radius:8px}
.client-inner{left:99px;top:902px;width:705px;height:81px;background:#fff;border-radius:6px;display:flex;align-items:center;justify-content:space-around;font-size:12px;font-weight:700;color:var(--teal-dark)}
.footer{left:0;top:1022px;width:900px;height:156px;background:linear-gradient(var(--foot-a),var(--foot-b))}
.footer h4{position:absolute;color:var(--cyan);font-weight:400;font-size:12px;text-transform:uppercase}
.footer ul{position:absolute;list-style:none;font-size:8.5px;color:#e4e8ec;line-height:17.3px}
.footer ul li:first-child{font-weight:700}
.footer .addr li{font-weight:700;color:#fff}
.divider{position:absolute;top:28px;width:1px;height:110px;background:rgba(255,255,255,.15)}
.social{position:absolute;left:748px;top:55px;display:flex;gap:6px}
.social i{width:12px;height:12px;border-radius:50%;background:#9aa6ae}
.copy{left:0;top:1178px;width:900px;height:22px;background:#e5e5e5;text-align:center;font-size:9px;line-height:22px;color:#222}
</style>
</head>
<body>
<div class="abs page"></div>
<div class="abs brand"><i></i>CorvinSoft Technologies</div>
<div class="abs search"><span>Search</span><span>&#9906;</span></div>

<nav class="abs nav">
  <a style="left:75px">HOME</a>
  <a class="active" style="left:185px">PRODUCTS</a>
  <a style="left:294px">SERVICES</a>
  <a style="left:382px">NEWS</a>
  <a style="left:479px">ABOUT US</a>
  <a style="left:611px">CONTACT US</a>
</nav>

<div class="abs hero-frame"></div>
<div class="abs hero-img" role="img" aria-label="Banner photos of drilling equipment against blue sky"></div>
<div class="abs hero-card">
  <h1>We develop software and associated<br>services to some of the world’s largest<br>oil companies</h1>
  <p>CVS have the tools to help companies to better manage the business of drilling wells</p>
</div>
<div class="abs btn-read">Continue Reading....</div>
<svg class="abs ribbon" width="140" height="40" viewBox="0 0 140 40">
  <polygon points="0,0 140,0 126,20 140,40 0,40 16,20" fill="#ececec"/>
  <circle cx="52" cy="14" r="4.5" fill="#17495a"/>
  <circle cx="68" cy="14" r="4.5" fill="#5ba9b5"/>
  <circle cx="84" cy="14" r="4.5" fill="#5ba9b5"/>
  <circle cx="100" cy="14" r="4.5" fill="#5ba9b5"/>
</svg>
<div class="abs dropdown"><a>TZQ</a><a>BLV</a><a>PNJ</a></div>

<h2 class="abs welcome">Welcome to CorvinSoft Technologies :</h2>
<div class="abs welcome-img" role="img" aria-label="Photo of a pump jack in a field"></div>
<div class="abs intro">
  <p>CorvinSoft Technologies have developed and continue to support software in over 30 countries, providing real results to hundreds of drilling operations.With decades of hands-on software and well engineering experience, we are uniquely positioned to provide the right solution to our customers.</p>
  <p>We are an integrated software and consulting organization, helping companies across the globe to better manage the Business of Drilling Wells, improving capital allocation and saving money.With BLV you can quickly reconcile wells and report costs to partners and confidence.</p>
</div>

<section class="abs col" style="left:102px">
  <h3>WHO WE ARE</h3>
  <div class="thumb" role="img" aria-label="Photo of work vessels at sea" style="background:linear-gradient(#b8cde2,#8aa7c6 55%,#c0553a 62%,#2f5f8f 70%)"></div>
  <p>Sed ut perspiciatis unde omnis iste<br>natus error sit voluptatem accusan-<br>tium doloremque laudantiumconse-</p>
  <div class="more">READ MORE</div>
</section>
<section class="abs col" style="left:282px">
  <h3>WHAT WE DO ?</h3>
  <div class="thumb" role="img" aria-label="Photo of a wellhead in red mud" style="background:linear-gradient(#6d3b2a,#b35a3c 50%,#c98a6a)"></div>
  <p>Sed ut perspiciatis unde omnis iste<br>natus error sit voluptatem accusan-<br>tium doloremque laudantiumconse-</p>
  <div class="more">READ MORE</div>
</section>
<section class="abs col" style="left:458px">
  <h3>HOW WE DO ?</h3>
  <div class="thumb" role="img" aria-label="Photo of pump jacks at sunset" style="background:linear-gradient(#3b3a44,#c97a35 55%,#2a1d16 80%)"></div>
  <p>Sed ut perspiciatis unde omnis iste<br>natus error sit voluptatem accusan-<br>tium doloremque laudantiumconse-</p>
  <div class="more">READ MORE</div>
</section>
<section class="abs col" style="left:635px">
  <h3>SERVICES</h3>
  <div class="thumb" role="img" aria-label="Photo of a drill and a spirit level" style="background:linear-gradient(135deg,#2d4f7a,#f0f0f0 45%,#f1c21b 60%,#e3a812)"></div>
  <p>Sed ut perspiciatis unde omnis iste<br>natus error sit voluptatem accusan-<br>tium doloremque laudantiumconse-</p>
  <div class="more">READ MORE</div>
</section>

<h2 class="abs clients">OUR CLIENTS :</h2>
<div class="abs client-box"></div>
<div class="abs client-inner">
  <span>VELO</span><span>Bramwell</span><span>Halvorn</span><span>Koruna</span><span>GN</span><span>FALUMI</span><span>Dunt</span><span>Tessaly</span><span>Marovel</span><span>VELO</span><span>Bramwell</span>
</div>

<footer class="abs footer">
  <h4 style="left:80px;top:20px">Quick Links :</h4>
  <ul style="left:82px;top:46px"><li>VESTIBULUM NON</li><li>Praesent vitae</li><li>Ut velit enim</li><li>Vestibulum non</li><li>Fermentum nec</li></ul>
  <ul style="left:185px;top:46px"><li>VESTIBULUM NON</li><li>Praesent vitae</li><li>Ut velit enim</li><li>Vestibulum non</li><li>Fermentum nec</li></ul>
  <ul style="left:291px;top:46px"><li>VESTIBULUM NON</li><li>Praesent vitae</li><li>Ut velit enim</li><li>Vestibulum non</li><li>Fermentum nec</li></ul>
  <span class="divider" style="left:388px"></span>
  <h4 style="left:423px;top:22px">Europe :</h4>
  <ul class="addr" style="left:424px;top:47px;line-height:18.7px"><li>12 Larchfield Row</li><li>Dunmore, DM4 2QT</li><li>Phone:+44(0)1632 960412</li><li>Email:eu@corvinsoft.example</li></ul>
  <span class="divider" style="left:556px"></span>
  <h4 style="left:576px;top:22px">North America :</h4>
  <ul class="addr" style="left:577px;top:47px;line-height:18.7px"><li>4100 Meridian Park Dr, Suite 210</li><li>Brackton, TX 70019</li><li>Phone:(555) 014 2278</li><li>Email:us@corvinsoft.example</li></ul>
  <span class="divider" style="left:716px"></span>
  <h4 style="left:736px;top:21px">Follow us:</h4>
  <div class="social"><i></i><i></i><i></i></div>
</footer>
<div class="abs copy">© Copyright 2012 All rights reserved.</div>
</body>
</html>
```